I am hosting a banquet called, Copper & Pearl Gala and I need a design to help sell it on Linkora.

Hi all.
No disco balls, please.
I would like a miser-traditional design, classy.

```html
<!DOCTYPE html>
<html lang="en">
<head>
<meta charset="UTF-8">
<title>Copper &amp; Pearl Gala</title>
<link href="https://fonts.googleapis.com/css2?family=Playfair+Display:wght@400;500&family=Great+Vibes&family=Poppins:wght@400;500&display=swap" rel="stylesheet">
<style>
  :root {
    --ink: #1c1c1c;
    --paper: #ffffff;
    --muted: #b5b5b5;
    --shadow: rgba(0,0,0,0.35);
  }
  * { margin: 0; padding: 0; box-sizing: border-box; }
  html, body { width: 1200px; height: 1200px; overflow: hidden; background: var(--paper); }
  .canvas { position: relative; width: 1200px; height: 1200px; background: var(--paper); }
  .card {
    position: absolute; left: 141px; top: 142px; width: 919px; height: 919px;
    background: var(--paper); box-shadow: 0 0 28px var(--shadow); overflow: hidden;
  }
  .card__dark { position: absolute; left: 0; top: 0; width: 400px; height: 100%; background: var(--ink); }
  .t { position: absolute; line-height: 1; white-space: nowrap; }
  .on-dark { color: var(--paper); }
  .on-light { color: var(--ink); }
  .serif { font-family: "Playfair Display", Georgia, serif; font-variant-numeric: lining-nums; }
  .sans { font-family: "Poppins", Arial, sans-serif; }
  .script { font-family: "Great Vibes", cursive; }
  h1 { font-weight: inherit; }

  .kicker { font-size: 23px; letter-spacing: 5px; top: 102px; }
  .kicker--left { right: 532px; }
  .kicker--right { left: 405px; }
  .title { font-size: 80px; font-weight: 500; top: 158px; letter-spacing: -1px; }
  .title--left { right: 540px; }
  .title--right { left: 417px; }
  .tagline { font-size: 68px; top: 280px; }
  .tagline--left { right: 540px; }
  .tagline--right { left: 405px; }

  .weekday { left: 91px; top: 394px; font-size: 29px; letter-spacing: 4px; }
  .day-badge {
    position: absolute; left: 96px; top: 432px; width: 80px; height: 80px; border-radius: 50%;
    background: var(--paper); color: var(--ink); display: flex; align-items: center; justify-content: center;
    font-family: "Playfair Display", Georgia, serif; font-variant-numeric: lining-nums; font-size: 36px;
  }
  .day-badge sup, .rsvp-badge sup { font-size: 0.5em; vertical-align: 0.9em; }
  .month { left: 189px; top: 434px; font-size: 36px; }
  .year-muted { left: 189px; top: 476px; font-size: 38px; color: var(--muted); }
  .schedule { left: 91px; font-size: 27px; }
  .schedule--social { top: 571px; }
  .schedule--dinner { top: 637px; }
  .ticket-label { left: 91px; top: 731px; font-size: 28px; line-height: 1.15; }
  .ticket-price { left: 210px; top: 726px; font-size: 84px; }
  .ticket-price sup { font-size: 0.45em; vertical-align: 1em; }
  .table-offer { left: 91px; top: 827px; font-size: 21px; font-weight: 500; display: flex; align-items: center; gap: 6px; }
  .table-offer__price {
    background: var(--paper); color: var(--ink); font-family: "Playfair Display", Georgia, serif;
    font-variant-numeric: lining-nums; font-size: 24px; padding: 1px 10px 2px; border-radius: 3px; line-height: 1;
  }
  .table-offer__price sup { font-size: 0.5em; vertical-align: 0.8em; }

  .label { font-size: 32px; }
  .venue-label { left: 423px; top: 400px; }
  .detail { left: 427px; font-size: 23px; }
  .detail--1 { top: 449px; }
  .detail--2 { top: 484px; }
  .divider { position: absolute; left: 431px; width: 318px; height: 12px; }
  .divider--1 { top: 535px; }
  .divider--2 { top: 714px; }
  .dress-label { left: 429px; top: 581px; }
  .detail--3 { left: 433px; top: 622px; }
  .detail--4 { left: 433px; top: 652px; }
  .rsvp-label { left: 425px; top: 764px; font-size: 24px; }
  .rsvp-line { position: absolute; top: 792px; left: 425px; display: flex; align-items: center; height: 74px; }
  .rsvp-word { font-family: "Playfair Display", Georgia, serif; font-variant-numeric: lining-nums; font-size: 32px; color: var(--ink); line-height: 1; }
  .rsvp-sep { width: 1px; height: 52px; background: var(--ink); margin: 0 14px; }
  .rsvp-badge {
    width: 74px; height: 74px; border-radius: 50%; background: var(--ink); color: var(--paper);
    display: flex; align-items: center; justify-content: center; margin-left: 12px;
    font-family: "Playfair Display", Georgia, serif; font-variant-numeric: lining-nums; font-size: 28px;
  }
</style>
</head>
<body>
<div class="canvas">
  <div class="card">
    <div class="card__dark"></div>

    <span class="t sans kicker kicker--left on-dark">Marlow</span>
    <span class="t sans kicker kicker--right on-light">Centennial</span>

    <h1>
      <span class="t serif title title--left on-dark">Copper &amp;</span>
      <span class="t serif title title--right on-light">Pearl Gala</span>
    </h1>

    <span class="t script tagline tagline--left on-dark">Join us</span>
    <span class="t script tagline tagline--right on-light">for the Celebration</span>

    <span class="t serif weekday on-dark">SATURDAY</span>
    <div class="day-badge">3<sup>rd</sup></div>
    <span class="t serif month on-dark">June</span>
    <span class="t serif year-muted">2023</span>

    <span class="t serif schedule schedule--social on-dark">Social Hour 6:00 p.m.</span>
    <span class="t serif schedule schedule--dinner on-dark">Dinner 7:00 p.m.</span>

    <span class="t sans ticket-label on-dark">TICKET<br>PRICE</span>
    <span class="t serif ticket-price on-dark"><sup>$</sup>30</span>
    <div class="t sans table-offer on-dark">TABLE FOR 8 <span class="table-offer__price"><sup>$</sup>250</span></div>

    <span class="t serif label venue-label on-light">VENUE</span>
    <span class="t sans detail detail--1 on-light">Marlow High School Gymnasium</span>
    <span class="t sans detail detail--2 on-light">218 Alder Street, Marlow, Kansas</span>

    <svg class="divider divider--1" viewBox="0 0 318 12" aria-hidden="true">
      <line x1="4" y1="6" x2="314" y2="6" stroke="#1c1c1c" stroke-width="1.5"/>
      <rect x="1" y="3" width="6" height="6" transform="rotate(45 4 6)" fill="#1c1c1c"/>
      <rect x="311" y="3" width="6" height="6" transform="rotate(45 314 6)" fill="#1c1c1c"/>
      <circle cx="159" cy="6" r="3" fill="#1c1c1c"/>
    </svg>

    <span class="t serif label dress-label on-light">DRESS CODE:</span>
    <span class="t sans detail detail--3 on-light">Copper &amp; Pearl Attire</span>
    <span class="t sans detail detail--4 on-light">Smart Casual to Fancy Formal</span>

    <svg class="divider divider--2" viewBox="0 0 318 12" aria-hidden="true">
      <line x1="4" y1="6" x2="314" y2="6" stroke="#1c1c1c" stroke-width="1.5"/>
      <rect x="1" y="3" width="6" height="6" transform="rotate(45 4 6)" fill="#1c1c1c"/>
      <rect x="311" y="3" width="6" height="6" transform="rotate(45 314 6)" fill="#1c1c1c"/>
      <circle cx="159" cy="6" r="3" fill="#1c1c1c"/>
    </svg>

    <span class="t sans rsvp-label on-light">RSVP</span>
    <div class="rsvp-line">
      <span class="rsvp-word">Monday</span>
      <span class="rsvp-sep"></span>
      <span class="rsvp-word">May</span>
      <div class="rsvp-badge">29<sup>th</sup></div>
      <span class="rsvp-sep"></span>
      <span class="rsvp-word">2023</span>
    </div>
  </div>
</div>
</body>
</html>
```